revised: 'kelvale ironworks' logo -or- business card

we require a business card or a logo that can be used on a business card & other stationery

(i've just recently decided to open this contest up to logo designs as well - but if you have already been working on a card concept, please feel free to continue with it & submit!)

-

We design and build custom brackets and fixings for our customers and their castles, i.e. homes, offices, workshops, farms etc. Our products might be used to:
- brace or support structures, such as houses, decks, small bridges, etc.
- connect any building material to another
- or could simply be a unique piece that exists as a talking point

As part of our design process we would produce drawings/plans/blue prints/prototypes of the product. Our designs factor in multiple elements, from the materials being joined, the client's taste, and the overall durability demanded by the application - if necessary, the bracket may also be endorsed by a third party, such as a stuctural or mechanical engineer.

The build process takes part in our workshop and on the client's site - some elements may be manufactured off-site, depending on the design chosen and the materials used.

Our brackets are designed to our customers' tastes and could be made to be hidden within the structure or exposed to create interest. Our brackets can be large or small, or be neat with clean lines or take on more of an industrial look.
Updates

please note brief has been updated with a more specific description of our business activity

i have also added the final drawing that was used to water-jet the bracket shown in the photos

also, you will note i changed the title to 'logo + business card'

i don't expect a logo as a discrete artefact of the job, however, i expect that some or all elements on the face of the business card will lend themselves to the street sign (as stated in the original brief) as well as any future logo used on letter heads, invoices, etcetera

another update - changed the allowable entries to include logo's only, as well as business cards

Industry/Entity Type

Industrial

Requirements
Must have
• the face should have the name 'Kelvale Ironworks' (or no/all-caps)

the number '75' in the logo, which will also be turned into a conservative (residential) street sign ('75' being a street number) - '75' should stand alone -OR- be readily identified by someone who has previously received a business card

i need to make this '75' and any associated 'framing', so it should be transferrable to cad/dxf for machining, laser/water-cutting, brazing/welding, etcet.

(on that note, the winning designer will be able to share their vision for this sign and we'll adhere to it ... within the realms of possibility! if you're happy with the result then you could include it in your portfolio)
Nice to have
• one side of the card needs a majority of space for quotes, hand-written information, etcet. so this side should be white or a light, complimentary colour suitable for black/blue pen

the following should appear somewhere on the card (there is no email or website) :
- name : Dana Morrow (Proprietor)
- mobile phone number : +61 (0) 498 761203
- abn: 58 904 617 235

any combination of the following (or equivalent) text:

* 'your castle' - this is slang for your house/place (i prefer this to 'home' as 1: it can apply to a place of business, and 2: for me at least, it conjurs images of wrought iron, brass, hardwood & stone)

* unique

* ...

```html
<!DOCTYPE html>
<html lang="en">
<head>
<meta charset="utf-8">
<title>Kelvale Ironworks – Business Card</title>
<link href="https://fonts.googleapis.com/css2?family=Roboto:wght@400;700&display=swap" rel="stylesheet">
<style>
  :root {
    --page: #ffffff;
    --card: #ffffff;
    --card-edge: #9a9a9a;
    --bronze: #8a6642;
    --band-rule: #2a1c10;
    --ink: #111111;
    --ink-soft: #555555;
    --ghost: #efebe5;
  }
  html, body {
    margin: 0;
    padding: 0;
    width: 845px;
    height: 1200px;
    overflow: hidden;
    background: var(--page);
    font-family: "Roboto", Arial, sans-serif;
  }
  .sheet {
    position: relative;
    width: 845px;
    height: 1200px;
  }
  .card {
    position: absolute;
    left: 181px;
    width: 487px;
    height: 317px;
    background: var(--card);
    box-sizing: border-box;
    border: 1px solid var(--card-edge);
    overflow: hidden;
  }
  .card--front { top: 252px; }
  .card--back { top: 652px; }
  .card__band {
    position: absolute;
    left: 0;
    top: 0;
    width: 68px;
    height: 100%;
    background: var(--bronze);
    border-right: 2px solid var(--band-rule);
    z-index: 2;
  }
  .brand-disc {
    position: absolute;
    left: 34px;
    top: 57px;
    width: 74px;
    height: 74px;
    z-index: 3;
  }
  .company-name {
    position: absolute;
    left: 133px;
    top: 77px;
    margin: 0;
    font-size: 26px;
    font-weight: 700;
    line-height: 1;
    color: var(--bronze);
    letter-spacing: 0.1px;
  }
  .tagline {
    position: absolute;
    left: 134px;
    top: 111px;
    margin: 0;
    font-size: 14.5px;
    font-weight: 400;
    line-height: 1;
    color: var(--ink-soft);
  }
  .contact {
    position: absolute;
    left: 134px;
    top: 185px;
    margin: 0;
    color: var(--ink);
    line-height: 1;
  }
  .contact__person {
    display: block;
    font-size: 18.5px;
    font-weight: 400;
    color: #333333;
    margin-bottom: 18px;
  }
  .contact__role {
    font-size: 14px;
  }
  .contact__line {
    display: block;
    font-size: 20px;
    font-weight: 400;
    margin-bottom: 5px;
  }
  .contact__line strong { font-weight: 700; }
  .back-ring {
    position: absolute;
    left: 0;
    top: 0;
    width: 100%;
    height: 100%;
  }
</style>
</head>
<body>
<main class="sheet">
  <section class="card card--front" aria-label="Business card front">
    <div class="card__band"></div>
    <svg class="brand-disc" viewBox="0 0 74 74" aria-hidden="true">
      <circle cx="37" cy="37" r="34.5" fill="#ffffff" stroke="#111111" stroke-width="3"/>
    </svg>
    <h1 class="company-name">Kelvale Ironworks</h1>
    <p class="tagline">Bespoke Bracket Manufacturing Service</p>
    <p class="contact">
      <span class="contact__person">Dana Morrow <span class="contact__role">(Proprietor)</span></span>
      <span class="contact__line">Abn: <strong>58 904 617 235</strong></span>
      <span class="contact__line">Mobile: <strong>+61 (0) 498 761203</strong></span>
    </p>
  </section>

  <section class="card card--back" aria-label="Business card back, space for notes">
    <svg class="back-ring" viewBox="0 0 487 317" aria-hidden="true">
      <circle cx="302" cy="179" r="200" fill="none" stroke="var(--ghost)" stroke-width="19"/>
    </svg>
    <div class="card__band"></div>
  </section>
</main>
</body>
</html>
```